Speisekarten-Design für gehobenes italienisches Restaurant
Zielgruppe
Wir sind ein gehobenes italienisches Restaurant und suchen ein neues Design für unsere Speisekarte. Wir haben ein eher älteres Publikum.
Aufgabenstellung
Wir möchten eine elegantes modernes Design. Einzelseiten im A4 Format.

```html
<!DOCTYPE html>
<html lang="de">
<head>
<meta charset="utf-8">
<title>Casa del Pino – Grazie</title>
<link rel="stylesheet" href="https://fonts.googleapis.com/css2?family=Open+Sans:wght@400;600;700&family=Libre+Baskerville:wght@400;700&family=Mrs+Saint+Delafield&display=swap">
<style>
  :root {
    --wine: #7b1428;
    --ink: #111111;
    --text-dark: #444444;
    --text-muted: #6a6a6a;
    --gold: #f6e890;
    --paper: #ffffff;
    --photo-dark: #3a3a3a;
    --photo-light: #b9b9b9;
  }
  * { margin: 0; padding: 0; box-sizing: border-box; }
  html, body { width: 848px; height: 1200px; overflow: hidden; background: var(--paper); }
  body { font-family: "Open Sans", Arial, sans-serif; color: var(--text-dark); }
  .page { position: relative; width: 848px; height: 1200px; }

  .team-photo {
    position: absolute; left: 18px; top: 20px; width: 807px; height: 348px;
    background: linear-gradient(90deg, var(--photo-dark) 0%, var(--photo-light) 35%, #d8d8d8 55%, var(--photo-light) 75%, var(--photo-dark) 100%);
  }

  .thanks { position: absolute; left: 0; top: 380px; width: 848px; height: 320px; text-align: center; }
  .thanks-script {
    position: absolute; left: 0; width: 848px; top: 12px;
    font-family: "Mrs Saint Delafield", cursive; font-size: 112px; line-height: 1;
    color: var(--wine); padding-left: 8px;
  }
  .thanks-title {
    position: absolute; left: 0; width: 848px; top: 108px;
    font-family: "Libre Baskerville", Georgia, serif; font-weight: 700;
    font-size: 28px; letter-spacing: 2px; color: var(--ink);
  }
  .thanks-message {
    position: absolute; left: 0; width: 848px; top: 164px;
    font-weight: 700; font-size: 13.5px; line-height: 23px; letter-spacing: 2.4px;
    text-transform: uppercase; color: var(--text-dark);
  }
  .thanks-signature {
    position: absolute; left: 0; width: 848px; top: 252px;
    font-family: "Mrs Saint Delafield", cursive; font-size: 52px; line-height: 1; color: var(--ink);
  }

  .menu-notes { position: absolute; left: 58px; top: 744px; width: 740px; }
  .note { position: absolute; left: 0; width: 740px; }
  .note-label {
    position: absolute; left: 0; top: 0;
    font-weight: 700; font-size: 13.5px; letter-spacing: 2.2px; color: var(--text-dark);
  }
  .note-text {
    position: absolute; left: 187px; top: 3px; width: 560px;
    font-size: 10.5px; line-height: 13px; color: var(--text-muted);
  }

  .site-footer {
    position: absolute; left: 0; top: 996px; width: 848px; height: 204px;
    background: var(--wine); color: var(--gold);
  }
  .footer-heading {
    font-family: "Libre Baskerville", Georgia, serif; font-size: 14.5px; line-height: 20px; color: var(--gold);
  }
  .opening-hours { position: absolute; left: 58px; top: 32px; }
  .hours-table { margin-top: 20px; font-size: 11.5px; letter-spacing: 1.4px; line-height: 17px; border-collapse: collapse; }
  .hours-table td { padding: 0; vertical-align: top; }
  .hours-table .day { width: 54px; }
  .hours-table .gap td { height: 8px; }

  .brand { position: absolute; left: 300px; top: 40px; width: 276px; text-align: center; }
  .brand-name { font-weight: 700; font-size: 30px; line-height: 40px; color: var(--gold); }
  .brand-sub { font-weight: 700; font-size: 14px; margin-top: 4px; color: var(--gold); }
  .website {
    position: absolute; left: 250px; top: 143px; width: 376px; text-align: center;
    font-size: 19px; font-weight: 600; letter-spacing: 2.6px;
  }

  .contact { position: absolute; left: 612px; top: 32px; }
  .address { margin-top: 20px; font-size: 12.5px; letter-spacing: 1.6px; line-height: 19px; }
  .phone { margin-top: 5px; font-size: 12.5px; letter-spacing: 1.6px; line-height: 19px; }
</style>
</head>
<body>
<main class="page">
  <div class="team-photo" role="img" aria-label="Schwarz-Weiß-Foto: lächelndes Restaurant-Team mit Schürzen und Kaffeetassen"></div>

  <section class="thanks">
    <div class="thanks-script">Grazie</div>
    <h1 class="thanks-title">PER LA TUA VISITA</h1>
    <p class="thanks-message">Wir sagen herzlichen Dank für Ihren Besuch bei uns!<br>Wir hoffen, dass Sie unsere Gastfreundschaft und unsere<br>kulinarischen Highlights genossen haben.</p>
    <p class="thanks-signature">Toni Ferraro &amp; das Casa-Team</p>
  </section>

  <section class="menu-notes">
    <div class="note" style="top:0">
      <span class="note-label">BESTELLSCHLUSS</span>
      <p class="note-text">für die Küche jeweils 30 Minuten vorher</p>
    </div>
    <div class="note" style="top:41px">
      <span class="note-label">PREISE</span>
      <p class="note-text">Die genannten Preise sind in EURO angegeben und beinhalten die Mehrwertsteuer<br>in der gesetzlich vorgeschriebenen Höhe.</p>
    </div>
    <div class="note" style="top:101px">
      <span class="note-label">DRUCKFEHLER</span>
      <p class="note-text">…sind bewusst in die Karte integriert worden. So können wir das Bedürfnis auch derjenigen Gäste stillen,<br>die immer auf der Suche nach Druckfehlern sind. Wir wünschen viel Spaß bei der Rätsel-Lösung<br>„Ei, wo sind sie denn?“.</p>
    </div>
    <div class="note" style="top:161px">
      <span class="note-label">STAND</span>
      <p class="note-text">© Januar 2024</p>
    </div>
    <div class="note" style="top:195px">
      <span class="note-label">COPYRIGHT</span>
      <p class="note-text">© Restaurant Casa del Pino. Anderweitige Verwendung untersagt. Änderungen bleiben uns vorbehalten.</p>
    </div>
  </section>

  <footer class="site-footer">
    <div class="opening-hours">
      <h2 class="footer-heading">Öffnungszeiten</h2>
      <table class="hours-table">
        <tr><td class="day">Mo – Fr</td><td>11:30 - 14:30 Uhr</td></tr>
        <tr><td></td><td>17:00 - 23:00 Uhr</td></tr>
        <tr class="gap"><td></td><td></td></tr>
        <tr><td class="day">Sa</td><td>11:30 - 14:30 Uhr</td></tr>
        <tr><td></td><td>17:00 - 24:00 Uhr</td></tr>
        <tr class="gap"><td></td><td></td></tr>
        <tr><td colspan="2">So &amp; Feiertag&nbsp;&nbsp;&nbsp;11:00 - 21:30 Uhr</td></tr>
      </table>
    </div>

    <div class="brand">
      <div class="brand-name">Casa del Pino</div>
      <div class="brand-sub">Ristorante • Pizzeria</div>
    </div>
    <div class="website">www.casa-del-pino.de</div>

    <div class="contact">
      <h2 class="footer-heading">Ristorante-Pizzeria<br>Casa del Pino</h2>
      <p class="address">Lindenallee 14<br>63500 Musterstadt-Süd</p>
      <p class="phone">Tel&nbsp;&nbsp;06100- 12 345 60<br>Fax&nbsp;&nbsp;06100- 12 345 61</p>
    </div>
  </footer>
</main>
</body>
</html>
```